New Webpage for High Class Expert Witness Services Company

We are looking for a minimalist design for a webpage that just has our logo and an entry form offer to connect with one of our Liaisons.
The entry form should just ask for Name, Email, Contact Info and Description of Project.

Company Name is: The Marlowe Crest Advisory Services

Number of Pages Required

1 page

```html
<!DOCTYPE html>
<html lang="en">
<head>
<meta charset="UTF-8">
<title>Connect With a Liaison – The Marlowe Crest Advisory Services</title>
<link href="https://fonts.googleapis.com/css2?family=Cinzel:wght@500;600&family=Poppins:wght@400;500;600&display=swap" rel="stylesheet">
<style>
  :root{
    --ink:#0a0a0a;
    --white:#ffffff;
    --muted:#8a8a8a;
    --line:#bdbdbd;
    --field-border:#c9c9c9;
    --logo-silver:#d9d9d9;
    --footer-rule:#3a3a3a;
    --bg-dark:#111111;
    --bg-mid:#3c3c3c;
  }
  *{box-sizing:border-box;margin:0;padding:0}
  html,body{width:1200px;height:935px;overflow:hidden}
  body{
    position:relative;
    font-family:"Poppins",sans-serif;
    background:var(--bg-dark);
    color:var(--ink);
  }
  .backdrop{
    position:absolute;inset:0;
    background:
      radial-gradient(ellipse 300px 200px at 140px 500px, rgba(160,160,160,.35), transparent 70%),
      radial-gradient(ellipse 320px 260px at 1020px 520px, rgba(130,130,130,.3), transparent 70%),
      linear-gradient(180deg,#161616 0%,#2e2e2e 45%,#262626 75%,#121212 100%);
  }
  .brand{
    position:absolute;top:72px;left:0;width:1200px;
    display:flex;justify-content:center;align-items:center;gap:14px;
  }
  .brand-mark{width:26px;height:26px;background:var(--logo-silver)}
  .brand-name{
    font-family:"Cinzel",serif;font-weight:600;font-size:26px;
    letter-spacing:1px;color:var(--logo-silver);
  }
  .card{
    position:absolute;left:296px;top:172px;width:608px;height:670px;
    background:var(--white);border-radius:20px;
    padding:0 60px;
  }
  .card-title{
    margin-top:40px;text-align:center;
    font-family:"Cinzel",serif;font-weight:600;font-size:30px;line-height:34px;
    letter-spacing:.5px;
  }
  .card-intro{
    margin-top:4px;text-align:center;font-size:13px;line-height:20px;padding:0 30px;
  }
  .divider{
    margin-top:18px;height:16px;display:flex;justify-content:center;align-items:center;gap:10px;
  }
  .divider span{width:135px;height:1px;background:var(--line)}
  .divider i{width:12px;height:12px;border-radius:50%;background:var(--line);display:block}
  .field-label{display:block;font-size:11.5px;line-height:16px;margin-top:13px;margin-bottom:8px}
  .field-label.first{margin-top:21px}
  .field{position:relative}
  .field svg{position:absolute;left:13px;top:15px;width:16px;height:16px;stroke:var(--muted);fill:none;stroke-width:1.3}
  .field input,.field textarea{
    width:100%;height:46px;border:1px solid var(--field-border);border-radius:7px;
    padding-left:37px;font-family:"Poppins",sans-serif;font-size:11.5px;color:var(--ink);
    background:var(--white);outline:none;
  }
  .field textarea{height:109px;padding-top:14px;resize:none}
  .field input::placeholder,.field textarea::placeholder{color:var(--muted)}
  .field.long .field-label{margin-bottom:10px}
  .submit{
    display:block;width:100%;height:53px;margin-top:18px;border:none;border-radius:6px;
    background:var(--ink);color:var(--white);font-family:"Poppins",sans-serif;
    font-weight:600;font-size:12px;letter-spacing:.2px;
  }
  .footer-rule{position:absolute;left:136px;top:880px;width:918px;height:1px;background:var(--footer-rule)}
  .footer-note{position:absolute;left:0;top:899px;width:1200px;text-align:center;color:var(--white);font-size:13px;line-height:18px}
</style>
</head>
<body>
  <div class="backdrop" role="img" aria-label="Dimmed black and white photo of a busy forensic laboratory with desks, lamps and workers"></div>

  <header class="brand">
    <div class="brand-mark"></div>
    <div class="brand-name">The Marlowe Crest Advisory Services</div>
  </header>

  <main class="card">
    <h1 class="card-title">CONNECT WITH A LIAISON</h1>
    <p class="card-intro">High-Class Expert Witness Support. Share Your Project Details And A Dedicated Liaison Will Reach You Within 24 Hours.</p>
    <div class="divider"><span></span><i></i><span></span></div>

    <form>
      <label class="field-label first" for="name">Full Name *</label>
      <div class="field">
        <svg viewBox="0 0 16 16"><circle cx="8" cy="5" r="3"/><path d="M2.5 15c0-3.2 2.5-5.2 5.5-5.2s5.5 2 5.5 5.2"/></svg>
        <input id="name" type="text" placeholder="First Name">
      </div>

      <label class="field-label" for="email">Email Address *</label>
      <div class="field">
        <svg viewBox="0 0 16 16"><path d="M1.5 6.5 8 2.5l6.5 4V14h-13z"/><path d="M1.5 6.5 8 10.5l6.5-4"/></svg>
        <input id="email" type="email" placeholder="Your Email">
      </div>

      <label class="field-label" for="phone">&nbsp;Contact Info (Phone / Direct Line) *</label>
      <div class="field">
        <svg viewBox="0 0 16 16"><path d="M3 1.8h2.4l1.2 3-1.5 1.2a8 8 0 0 0 4.9 4.9l1.2-1.5 3 1.2v2.4c0 .8-.7 1.3-1.4 1.2A12.5 12.5 0 0 1 1.8 3.2C1.7 2.5 2.2 1.8 3 1.8z"/><path d="M11 1.5v3M13.5 1.5v3"/></svg>
        <input id="phone" type="tel" placeholder="Phone">
      </div>

      <label class="field-label" for="project">Description Of Project *</label>
      <div class="field">
        <svg viewBox="0 0 16 16"><path d="M8 1.8c3.6 0 6.3 2.5 6.3 5.6S11.6 13 8 13c-.9 0-1.7-.1-2.5-.4L2 14l1.1-2.8C2.2 10.2 1.7 8.9 1.7 7.4 1.7 4.3 4.4 1.8 8 1.8z"/><path d="M5 6.3h6M5 8.6h4"/></svg>
        <textarea id="project" placeholder="Provide Key Case Details, Litigation Area, Required Expertise, Deadlines..."></textarea>
      </div>

      <button class="submit" type="button">SUBMIT NOW</button>
    </form>
  </main>

  <div class="footer-rule"></div>
  <p class="footer-note">2026 The Marlowe Crest Advisory Services All Right</p>
</body>
</html>
```